Redesign for a start up airline technology. The website is quelbrion.com.

I need a PowerPoint template that complements our website. I can provide our current template as a starting point.

```html
<!DOCTYPE html>
<html lang="en">
<head>
<meta charset="utf-8">
<title>Quelbrion — Presentation Template</title>
<link href="https://fonts.googleapis.com/css2?family=Oswald:wght@500;600&family=Lexend:wght@300;400&family=Montserrat:wght@700&display=swap" rel="stylesheet">
<style>
  :root {
    --canvas: #e1e4e8;
    --navy-deep: #07143a;
    --navy: #0d2a6b;
    --navy-mid: #1b3f86;
    --brand-blue: #123f9a;
    --accent-blue: #1a8ee0;
    --title-grey: #8392b0;
    --panel-light: #eef0f3;
    --panel-mist: #d6dbe2;
    --white: #ffffff;
    --body-white: #e6ebf5;
  }
  * { margin: 0; padding: 0; box-sizing: border-box; }
  html, body { width: 1200px; height: 900px; overflow: hidden; background: var(--canvas); }
  .board { position: relative; width: 1200px; height: 900px; }
  .slide {
    position: absolute; width: 443px; height: 249px; overflow: hidden;
    background: linear-gradient(180deg, var(--navy-mid) 0%, var(--navy) 45%, var(--navy-deep) 100%);
    box-shadow: 4px 6px 10px rgba(0,0,0,.35);
    font-family: "Lexend", sans-serif;
  }
  .col-left { left: 126px; } .col-right { left: 594px; }
  .row-1 { top: 60px; } .row-2 { top: 336px; } .row-3 { top: 606px; }

  .backdrop { position: absolute; inset: 0; }
  .backdrop-city { background: radial-gradient(ellipse at 50% 70%, #1f4a95 0%, #0d2a6b 45%, #061235 100%); }

  .panel {
    position: absolute; left: 0; top: 0; width: 443px;
    border-radius: 0 0 30px 30px;
    background: linear-gradient(180deg, var(--panel-light) 0%, var(--panel-mist) 100%);
  }
  .panel-tall { height: 121px; }
  .panel-short { height: 59px; border-radius: 0 0 22px 22px; }
  .panel-clouds { background: radial-gradient(ellipse at 45% 40%, #ffffff 0%, #dfe3e7 45%, #b9c3c9 100%); }

  .wordmark { position: absolute; font-family: "Lexend", sans-serif; font-weight: 400; color: var(--brand-blue); }
  .wordmark-small { top: 14px; right: 14px; font-size: 11px; }

  .display-title {
    position: absolute; left: 0; right: 0; text-align: center;
    font-family: "Oswald", sans-serif; font-weight: 600; color: var(--title-grey);
  }
  .display-about { top: 28px; font-size: 56px; letter-spacing: 14px; line-height: 1; }
  .display-objective { top: 36px; font-size: 56px; letter-spacing: 16px; line-height: 1; }

  .section-title {
    position: absolute; font-family: "Oswald", sans-serif; font-weight: 600;
    color: var(--brand-blue); font-size: 23px; line-height: 1;
  }
  .title-centered { left: 0; right: 0; text-align: center; top: 22px; }
  .title-chart { left: 156px; top: 22px; }

  .body-copy { position: absolute; color: var(--body-white); font-weight: 300; font-size: 6.4px; line-height: 10px; text-align: justify; }
  .body-objective { left: 43px; top: 139px; width: 357px; }
  .body-title { left: 43px; top: 80px; width: 357px; }
  .body-about { left: 36px; top: 134px; width: 371px; text-align: center; font-size: 7.2px; line-height: 10px; letter-spacing: .8px; }

  .copyright { position: absolute; left: 8px; bottom: 8px; font-size: 4.2px; color: var(--body-white); }

  .cover-heading { position: absolute; font-family: "Oswald", sans-serif; font-weight: 600; line-height: 1; }
  .cover-sub { position: absolute; font-family: "Montserrat", sans-serif; font-weight: 700; font-size: 11px; }
  .opening .cover-heading { left: 35px; top: 20px; font-size: 24px; color: var(--brand-blue); }
  .opening .cover-sub { left: 34px; top: 52px; color: var(--brand-blue); }
  .opening .wordmark { left: 222px; top: 172px; font-size: 34px; color: var(--white); }

  .closing .cover-heading { left: 31px; top: 40px; font-size: 26px; color: var(--white); }
  .closing .cover-sub { left: 31px; top: 73px; color: var(--white); }
  .closing .wordmark { left: 150px; top: 152px; font-size: 40px; color: var(--brand-blue); }

  .curves { position: absolute; inset: 0; }
  .chart { position: absolute; inset: 0; }
  .chart text { font-family: "Lexend", sans-serif; fill: var(--white); font-size: 7px; }
</style>
</head>
<body>
<main class="board">

  <!-- Opening slide -->
  <section class="slide opening col-left row-1">
    <div class="backdrop backdrop-city" role="img" aria-label="Dark blue photo of a digital aircraft interface screen"></div>
    <svg class="curves" viewBox="0 0 443 249" width="443" height="249">
      <defs>
        <linearGradient id="openLight" x1="0" y1="0" x2="1" y2="0">
          <stop offset="0" stop-color="#e8ebef"/><stop offset="1" stop-color="#d2d8e0"/>
        </linearGradient>
      </defs>
      <path d="M0 0 H443 V0 L428 0 C380 90 230 165 110 163 C60 162 20 145 0 118 Z" fill="url(#openLight)" role="img" aria-label="Light photo of an aircraft in the sky"/>
      <path d="M0 124 C30 158 80 172 130 170 C250 165 380 95 430 0" fill="none" stroke="#1a8ee0" stroke-width="3"/>
      <path d="M0 130 C30 166 80 178 130 176 C250 172 392 98 443 0" fill="none" stroke="#0d2a6b" stroke-width="1.4" opacity=".6"/>
    </svg>
    <h1 class="cover-heading">LOREM IPSUM</h1>
    <p class="cover-sub">LOREM IPSUM</p>
    <p class="wordmark">Quelbrion</p>
  </section>

  <!-- About us slide -->
  <section class="slide col-right row-1">
    <div class="backdrop backdrop-city" role="img" aria-label="Dark blue photo of a city with a digital runway platform"></div>
    <div class="panel panel-tall" role="img" aria-label="Light photo of an aircraft on a futuristic platform"></div>
    <p class="wordmark wordmark-small">Quelbrion</p>
    <h2 class="display-title display-about">ABOUT US</h2>
    <p class="body-copy body-about">Quelbrion is an aerospace technology company that produces a game changing onboard weight and balance measurement system – the Gear Load Sensing System (GLSS). The GLSS hardware kit automatically calculates an aircraft's weight and center of gravity for each flight.<br>With numerous design, process and method patents, Quelbrion brings a unique combination of engineering innovation and certification expertise within the airline and aerospace industries.</p>
    <p class="copyright">© Quelbrion, LLC. All Rights Reserved.</p>
  </section>

  <!-- Objective slide -->
  <section class="slide col-left row-2">
    <div class="backdrop" role="img" aria-label="Deep blue gradient background"></div>
    <div class="panel panel-tall panel-clouds" role="img" aria-label="Photo of soft white clouds"></div>
    <p class="wordmark wordmark-small">Quelbrion</p>
    <h2 class="display-title display-objective">OBJECTIVE</h2>
    <p class="body-copy body-objective">Lorem ipsum dolor sit amet, consectetur adipiscing elit. Sed faucibus consectetur ultricies. Sed eget ipsum vitae urna dapibus dignissim. Pellentesque a arcu eget quam ullamcorper auctor eget iaculis quam. Maecenas tincidunt, arcu vel posuere ullamcorper, massa lectus sagittis enim, ac finibus ante metus eu urna. Quisque varius eget ligula ut iaculis. Vivamus vitae nibh imperdiet, luctus mi in, porta nibh. Donec libero nunc, condimentum quis sollicitudin quis, sagittis sit amet enim. Vivamus et neque diam. Proin nec posuere tellus. Etiam sed tincidunt orci. Curabitur vitae turpis vel quam mollis fermentum id quis tellus. Fusce ut dui turpis. Aliquam at nisi ut felis imperdiet fermentum maximus non diam. Fusce euismod ut purus vel pharetra.</p>
    <p class="copyright">© Quelbrion, LLC. All Rights Reserved.</p>
  </section>

  <!-- Title and text slide -->
  <section class="slide col-right row-2">
    <div class="backdrop backdrop-city" role="img" aria-label="Dark blue photo of a city with a digital runway platform"></div>
    <div class="panel panel-short" role="img" aria-label="Light photo of an aircraft on a futuristic platform"></div>
    <p class="wordmark wordmark-small">Quelbrion</p>
    <h2 class="section-title title-centered">TITLE</h2>
    <p class="body-copy body-title">Lorem ipsum dolor sit amet, consectetur adipiscing elit. Sed faucibus consectetur ultricies. Sed eget ipsum vitae urna dapibus dignissim. Pellentesque a arcu eget quam ullamcorper auctor eget iaculis quam. Maecenas tincidunt, arcu vel posuere ullamcorper, massa lectus sagittis enim, ac finibus ante metus eu urna. Quisque varius eget ligula ut iaculis. Vivamus vitae nibh imperdiet, luctus mi in, porta nibh. Donec libero nunc, condimentum quis sollicitudin quis, sagittis sit amet enim. Vivamus et neque diam. Proin nec posuere tellus. Etiam sed tincidunt orci. Curabitur vitae turpis vel quam mollis fermentum id quis tellus. Fusce ut dui turpis. Aliquam at nisi ut felis imperdiet fermentum maximus non diam. Fusce euismod ut purus vel pharetra.</p>
    <p class="copyright">© Quelbrion, LLC. All Rights Reserved.</p>
  </section>

  <!-- Bar chart slide -->
  <section class="slide col-left row-3">
    <div class="backdrop backdrop-city" role="img" aria-label="Dark blue photo of a city with a digital runway platform"></div>
    <div class="panel panel-short" role="img" aria-label="Light photo of an aircraft on a futuristic platform"></div>
    <p class="wordmark wordmark-small">Quelbrion</p>
    <h2 class="section-title title-chart">BAR CHART</h2>
    <svg class="chart" viewBox="0 0 443 249" width="443" height="249">
      <defs>
        <linearGradient id="barFill" x1="0" y1="0" x2="0" y2="1">
          <stop offset="0" stop-color="#ffffff"/><stop offset=".55" stop-color="#aab8d6" stop-opacity=".7"/><stop offset="1" stop-color="#1b3f86" stop-opacity=".2"/>
        </linearGradient>
      </defs>
      <g stroke="#ffffff" stroke-width=".8">
        <line x1="90" y1="77" x2="90" y2="216"/>
        <line x1="90" y1="216" x2="393" y2="216"/>
      </g>
      <g fill="#ffffff">
        <circle cx="90" cy="77" r="1.4"/><circle cx="90" cy="91" r="1.4"/><circle cx="90" cy="105" r="1.4"/><circle cx="90" cy="119" r="1.4"/><circle cx="90" cy="133" r="1.4"/><circle cx="90" cy="147" r="1.4"/><circle cx="90" cy="160" r="1.4"/><circle cx="90" cy="174" r="1.4"/><circle cx="90" cy="188" r="1.4"/><circle cx="90" cy="202" r="1.4"/><circle cx="90" cy="216" r="1.4"/>
      </g>
      <g text-anchor="end">
        <text x="84" y="80">100</text><text x="84" y="94">90</text><text x="84" y="108">80</text><text x="84" y="122">70</text><text x="84" y="136">60</text><text x="84" y="150">50</text><text x="84" y="163">40</text><text x="84" y="177">30</text><text x="84" y="191">20</text><text x="84" y="205">10</text><text x="84" y="219">0</text>
      </g>
      <g fill="url(#barFill)">
        <rect x="111" y="130" width="19" height="86"/>
        <rect x="146" y="102" width="19" height="114"/>
        <rect x="182" y="149" width="19" height="67"/>
        <rect x="218" y="91" width="19" height="125"/>
        <rect x="254" y="127" width="19" height="89"/>
        <rect x="291" y="152" width="19" height="64"/>
        <rect x="328" y="126" width="19" height="90"/>
        <rect x="364" y="127" width="19" height="89"/>
      </g>
      <g text-anchor="middle">
        <text x="120" y="227">2012</text><text x="155" y="227">2013</text><text x="191" y="227">2014</text><text x="227" y="227">2015</text><text x="263" y="227">2016</text><text x="300" y="227">2017</text><text x="337" y="227">2018</text><text x="373" y="227">2019</text>
      </g>
    </svg>
    <p class="copyright">© Quelbrion, LLC. All Rights Reserved.</p>
  </section>

  <!-- Closing slide -->
  <section class="slide closing col-right row-3">
    <div class="backdrop backdrop-city" role="img" aria-label="Dark blue photo of a digital aircraft interface screen"></div>
    <svg class="curves" viewBox="0 0 443 249" width="443" height="249">
      <defs>
        <linearGradient id="closeLight" x1="0" y1="0" x2="1" y2="1">
          <stop offset="0" stop-color="#d9dfe7"/><stop offset="1" stop-color="#f1f3f6"/>
        </linearGradient>
      </defs>
      <path d="M10 249 C60 150 160 90 260 82 C340 76 400 100 443 130 V249 Z" fill="url(#closeLight)" role="img" aria-label="Light photo of an aircraft interface screen"/>
      <path d="M4 249 C55 145 160 84 260 76 C340 70 405 96 435 124" fill="none" stroke="#1a8ee0" stroke-width="3"/>
    </svg>
    <h2 class="cover-heading">THANK YOU</h2>
    <p class="cover-sub">QUELBRION</p>
    <p class="wordmark">Quelbrion</p>
  </section>

</main>
</body>
</html>
```